Powepoint Templates From Logo

We need 3 Powerpoint templates for use in a variety of presentations we develop and customize. Primary uses of the powerpoint presentations are for printed "pitch books" describing our firm's capabilities and approach (a lot of words with some design elements that we have developed), printed presentations of the results of financial evaluations of our clients (lots of charts and graphs) and as the talking points for speeches.

The design needs to be professional and "solid" to establish that we are capable of selling your multi-million dollar business, but also be a little different to show that we are not just boring MBA's.

Our current website and other materials have been developed internally and leave a great deal to be desired. I have initiated this project to demonstrate how much our look can be improved and, if successful, I hope to do much bigger projects in the future.
Updates

This is my first project and I thaank you all for your participation. Since I am new to this, I don;t know if I am providing the help and feedback as I should. Please feel free to let me know how I can be a better customer.

Target Market(s)

professionals (lawyers, accountaants), business owners, business groups, technology people

Industry/Entity Type

Financial

Requirements
Must have
• our logo
a place where logo of client can be inserted if appropriate
templates for the following pages
title page
standard bullet narrative page
page for charts and graphs to mostly fill the page
Should not have a lot of dark solid color that has to be printed.

Nice to have
• something to perk up the color a little

```html
<!DOCTYPE html>
<html lang="en">
<head>
<meta charset="utf-8">
<title>Project Title – Chart Page</title>
<link href="https://fonts.googleapis.com/css2?family=Anton&family=Arimo:wght@400;700&display=swap" rel="stylesheet">
<style>
  :root {
    --navy: #0d2a63;
    --navy-deep: #0a2254;
    --ink: #111111;
    --rule-grey: #dcdfe4;
    --bg-top: #ffffff;
    --bg-bottom: #e6eefa;
    --header-left: #e3ecfb;
    --header-right: #ffffff;
    --shelf-top: #e4e4e4;
    --shelf-front: #c4c4c4;
  }
  * { margin: 0; padding: 0; box-sizing: border-box; }
  html, body { width: 1200px; height: 900px; overflow: hidden; }
  body {
    font-family: "Arimo", Arial, sans-serif;
    color: var(--ink);
    background: #ffffff;
  }
  .slide {
    position: relative;
    width: 1200px;
    height: 900px;
    overflow: hidden;
    background: linear-gradient(180deg, var(--bg-top) 10%, var(--bg-bottom) 100%);
  }
  .slide-header {
    position: absolute;
    left: 0; top: 0;
    width: 1200px; height: 97px;
    background: linear-gradient(90deg, var(--header-left) 0%, var(--header-right) 75%);
    border-bottom: 8px solid var(--rule-grey);
  }
  .slide-title {
    position: absolute;
    right: 27px; top: 18px;
    font-family: "Anton", "Arial Narrow", sans-serif;
    font-size: 46px;
    font-weight: 400;
    line-height: 1;
    letter-spacing: 0.5px;
    color: var(--navy);
  }
  .sub-heading {
    position: absolute;
    left: 104px; top: 141px;
    font-size: 27px;
    font-weight: 700;
  }
  .bullet-list {
    position: absolute;
    left: 70px; top: 192px;
    list-style: none;
  }
  .bullet-list li {
    display: flex;
    align-items: center;
    height: 56.5px;
    font-size: 29px;
  }
  .bullet-list svg { width: 18px; height: 22px; margin-right: 15px; flex: none; }
  .chart {
    position: absolute;
    left: 0; top: 450px;
    width: 810px; height: 300px;
  }
  .chart .value {
    font-family: "Anton", "Arial Narrow", sans-serif;
    font-size: 15px;
    fill: var(--ink);
    text-anchor: middle;
  }
  .chart-caption {
    position: absolute;
    left: 168px; top: 715px;
    font-size: 17px;
  }
  .footer-rule {
    position: absolute;
    left: 0; top: 842px;
    width: 1200px; height: 3px;
    background: var(--navy-deep);
  }
  .page-number {
    position: absolute;
    left: 40px; top: 862px;
    font-size: 21px;
  }
  .brand-name {
    position: absolute;
    right: 32px; top: 800px;
    font-size: 32px;
    font-weight: 700;
    line-height: 1;
    color: var(--navy);
    letter-spacing: 0.5px;
  }
</style>
</head>
<body>
<main class="slide">
  <header class="slide-header">
    <h1 class="slide-title">PROJECT TITLE HERE</h1>
  </header>

  <h2 class="sub-heading">SUB TEXT HERE</h2>

  <ul class="bullet-list">
    <li><svg viewBox="0 0 18 22" aria-hidden="true"><path d="M2 1 L10 1 L17 11 L10 21 L2 21 L9 11 Z" fill="var(--navy)"/></svg>Lorem ipsum dolor sit ipsum, Lorem ipsum dolor sit ipsum</li>
    <li><svg viewBox="0 0 18 22" aria-hidden="true"><path d="M2 1 L10 1 L17 11 L10 21 L2 21 L9 11 Z" fill="var(--navy)"/></svg>Lorem ipsum dolor sit ipsum, Lorem ipsum dolor sit ipsum</li>
    <li><svg viewBox="0 0 18 22" aria-hidden="true"><path d="M2 1 L10 1 L17 11 L10 21 L2 21 L9 11 Z" fill="var(--navy)"/></svg>Lorem ipsum dolor sit ipsum Lorem ipsum dolor sit ipsum</li>
  </ul>

  <svg class="chart" viewBox="0 300 540 200" role="img" aria-label="Bar chart with seven values">
    <polygon points="34,438 526,438 522,444 28,444" fill="var(--shelf-top)"/>
    <rect x="26" y="444" width="500" height="13" fill="var(--shelf-front)"/>

    <polygon points="38,329 46,320 92,320 84,329" fill="#c6e65a"/>
    <polygon points="84,329 92,320 92,440 84,448" fill="#6a9a00"/>
    <rect x="38" y="329" width="46" height="119" fill="#9fd100"/>
    <text class="value" x="72" y="314">000</text>

    <polygon points="112,424 118,419 164,419 157,424" fill="#ff7a7a"/>
    <polygon points="157,424 164,419 164,443 157,448" fill="#a80000"/>
    <rect x="112" y="424" width="45" height="24" fill="#ee1111"/>
    <text class="value" x="144" y="412">000</text>

    <polygon points="179,429 184,425 231,425 224,429" fill="#8fd0ff"/>
    <polygon points="224,429 231,425 231,443 224,448" fill="#0a6fbf"/>
    <rect x="179" y="429" width="45" height="19" fill="#1aa3ff"/>
    <text class="value" x="206" y="418">000</text>

    <polygon points="246,400 253,391 298,391 291,400" fill="#5f8fdc"/>
    <polygon points="291,400 298,391 298,440 291,448" fill="#06327a"/>
    <rect x="246" y="400" width="45" height="48" fill="#0a4aad"/>
    <text class="value" x="276" y="383">000</text>

    <polygon points="319,377 326,369 377,369 369,377" fill="#f4a46a"/>
    <polygon points="369,377 377,369 377,440 369,448" fill="#b35300"/>
    <rect x="319" y="377" width="50" height="71" fill="#ff7a00"/>
    <text class="value" x="349" y="362">000</text>

    <polygon points="395,429 400,425 447,425 440,429" fill="#ffe27a"/>
    <polygon points="440,429 447,425 447,443 440,448" fill="#b38a00"/>
    <rect x="395" y="429" width="45" height="19" fill="#ffc800"/>
    <text class="value" x="424" y="420">000</text>

    <polygon points="462,437 467,434 515,434 508,437" fill="#6fe0a0"/>
    <polygon points="508,437 515,434 515,443 508,448" fill="#007a3a"/>
    <rect x="462" y="437" width="46" height="11" fill="#00b35a"/>
    <text class="value" x="490" y="429">000</text>
  </svg>

  <p class="chart-caption">Lorem ipsum dolor sit ipsum, Lorem ipsum dolor sit ipsum</p>

  <p class="brand-name">ORVELLE KADE ADVISORY</p>

  <div class="footer-rule"></div>
  <p class="page-number">PAGE 2 OF 2</p>
</main>
</body>
</html>
```